Physiotherapy Referral Pad

-Need a referral pad for physiotherapy to be provided to doctors' offices. I would like it to be simple, not too cluttered and sharp looking so doctors can quickly complete it for clients.

-I have attached my logo which I would like to include. I have also included my business cards to keep the style, font, colors etc consistent.

-I would like to include my slogan
From Our Home To Yours

-I would like it to include services options with tick boxes for Mobile, Clinic, Telehealth, NRPDLA

-I would like for it to say Call to Book or Book Online

-I would like it to include my clinic address:
472 Marrow Crescent
Whitehorse, YT
Y2B3K9

-I would like it to include my contact info:
Glen Ostrow BSc(kin), MPT, CAFCI, IMS
(867)555-0142
physio@ostrowtherapy.ca

-I would like lines for the following:
Patient Name:
Diagnosis/Recommendations:
(extra lines to fill out patient info)

Physician Signature
Date

Target Market(s)

Physicians to refer clients to physiotherapy

Industry/Entity Type

Physical Therapy

Requirements
Must have
• Clean, concise, easy to look at and find pertinant categories for physicians
Nice to have
• Ostrow Therapy color scheme. Please see business cards and website as needed
Should not have
• Not too cluttered or wordy

```html
<!DOCTYPE html>
<html lang="en">
<head>
<meta charset="utf-8">
<title>Ostrow Therapy – Referral Pad</title>
<link rel="stylesheet" href="https://fonts.googleapis.com/css2?family=Libre+Baskerville:wght@400;700&family=Montserrat:wght@500&display=swap">
<style>
  :root {
    --navy: #263f8e;
    --green: #1d5e36;
    --rule: #555a66;
    --paper: #ffffff;
    --backdrop: #ffffff;
  }
  * { box-sizing: border-box; margin: 0; padding: 0; }
  html, body { width: 1200px; height: 1200px; overflow: hidden; background: var(--backdrop); }
  .pad {
    position: absolute; left: 243px; top: 96px; width: 714px; height: 1008px;
    background: var(--paper); border: 1px solid #e4e4e8;
    font-family: "Libre Baskerville", Georgia, serif;
  }
  .brand {
    position: absolute; left: 58px; top: 104px;
    display: flex; align-items: center; gap: 8px;
  }
  .brand-mark { width: 12px; height: 12px; background: var(--green); flex: none; }
  .brand-name { color: var(--green); font-weight: 700; font-size: 18px; line-height: 1.2; white-space: nowrap; }
  .contact {
    position: absolute; left: 464px; top: 78px; font-style: normal;
    font-family: "Montserrat", Arial, sans-serif; font-weight: 500;
    font-size: 13px; color: #4a4a52; line-height: 1.2;
  }
  .contact .address { margin-bottom: 6px; }
  .contact-item { display: flex; align-items: center; gap: 5px; margin-bottom: 4px; }
  .contact-item svg { width: 11px; height: 11px; flex: none; }
  .practitioner { position: absolute; left: 0; right: 0; top: 296px; text-align: center; }
  .practitioner-name { color: var(--green); font-weight: 700; font-size: 31px; letter-spacing: 1px; text-transform: uppercase; }
  .credentials { color: var(--navy); font-weight: 700; font-size: 15px; margin-top: 2px; font-variant: small-caps; letter-spacing: .5px; }
  .services {
    position: absolute; left: 0; right: 0; top: 372px;
    display: flex; justify-content: center; gap: 12px;
    color: var(--navy); font-size: 18px; text-transform: uppercase; letter-spacing: .5px;
  }
  .service { display: flex; align-items: center; gap: 7px; }
  .tickbox { width: 18px; height: 18px; border: 2px solid var(--green); }
  .field { position: absolute; display: flex; align-items: flex-end; gap: 10px; }
  .field-label { color: var(--navy); font-weight: 700; font-size: 20px; font-variant: small-caps; letter-spacing: .8px; white-space: nowrap; }
  .field-label.caps { font-size: 18px; letter-spacing: .6px; }
  .field-line { flex: 1; border-bottom: 1px solid var(--rule); height: 1px; margin-bottom: 4px; }
  .rule { position: absolute; border-bottom: 1px solid var(--rule); }
  .booking {
    position: absolute; left: 0; right: 0; top: 920px; text-align: center;
    color: var(--green); font-weight: 700; font-size: 21px; font-variant: small-caps; letter-spacing: 3px;
  }
  .slogan-band {
    position: absolute; left: 0; right: 0; bottom: 0; height: 46px; background: var(--navy);
    display: flex; align-items: center; justify-content: center;
    color: #fff; font-weight: 700; font-size: 18px; letter-spacing: 4px; text-transform: uppercase;
  }
</style>
</head>
<body>
<main class="pad">
  <div class="brand">
    <span class="brand-mark"></span>
    <span class="brand-name">Ostrow Therapy</span>
  </div>

  <address class="contact">
    <div class="address">472 Marrow Crescent<br>Whitehorse, YT Y2B3K9</div>
    <div class="contact-item">
      <svg viewBox="0 0 12 12"><circle cx="6" cy="6" r="6" fill="#1d5e36"/><path d="M4 3.2l1 1.4-.6.7c.4.9 1 1.5 1.9 1.9l.7-.6 1.4 1-.5 1.1C5.6 8.6 3.4 6.4 3 4z" fill="#fff"/></svg>
      (867)555-0142
    </div>
    <div class="contact-item">
      <svg viewBox="0 0 12 12"><circle cx="6" cy="6" r="6" fill="#1d5e36"/><rect x="3" y="4" width="6" height="4.2" fill="none" stroke="#fff" stroke-width=".9"/><path d="M3 4l3 2.3L9 4" fill="none" stroke="#fff" stroke-width=".9"/></svg>
      physio@ostrowtherapy.ca
    </div>
    <div class="contact-item">
      <svg viewBox="0 0 12 12"><circle cx="6" cy="6" r="6" fill="#1d5e36"/><circle cx="6" cy="6" r="3" fill="none" stroke="#fff" stroke-width=".9"/><path d="M3 6h6M6 3v6" stroke="#fff" stroke-width=".7"/></svg>
      www.ostrowtherapy.ca
    </div>
  </address>

  <header class="practitioner">
    <h1 class="practitioner-name">Glen Ostrow</h1>
    <p class="credentials">BSc(kin), MPT, CAFCI, IMS</p>
  </header>

  <div class="services">
    <span class="service"><span class="tickbox"></span>Mobile</span>
    <span class="service"><span class="tickbox"></span>Clinic</span>
    <span class="service"><span class="tickbox"></span>Telehealth</span>
    <span class="service"><span class="tickbox"></span>NRPDLA</span>
  </div>

  <div class="field" style="left:74px; width:564px; top:444px;">
    <span class="field-label caps">PATIENT NAME:</span><span class="field-line"></span>
  </div>
  <div class="rule" style="left:73px; width:564px; top:526px;"></div>

  <div class="field" style="left:74px; width:564px; top:563px;">
    <span class="field-label">Diagnosis/Recommendations:</span><span class="field-line"></span>
  </div>
  <div class="rule" style="left:73px; width:564px; top:644px;"></div>
  <div class="rule" style="left:76px; width:564px; top:703px;"></div>

  <div class="field" style="left:76px; width:562px; top:751px;">
    <span class="field-label">Physician Signature</span><span class="field-line"></span>
  </div>
  <div class="field" style="left:76px; width:562px; top:810px;">
    <span class="field-label">Date</span><span class="field-line"></span>
  </div>

  <p class="booking">Call to Book or Book Online</p>
  <footer class="slogan-band">From Our Home to Yours</footer>
</main>
</body>
</html>
```